New website: Wanderfjordia.com

We need to build a website for our small travel agency.
We want to be able to upload our brochures and offer our tours on site. No online payments involved yet.

We want to create an exact copy of another website: www.trekvalora.is, but with our own information and products. We like that design very much.

We are not going to do any sales via the website as the website above, but instead we want to show in the same style and everything the different tours that we offer.

We need to be able to modify tours: tour pictures, info, add videos, text, etc.

We need the website in English and Spanish. We can provide the Spanish translation.

We would advice you to create a copy of that website, with the text to be editable by us.
We own the website www.wanderfjordia.com and need that the designer uploads it and makes it work as well.

We have uploaded some pictures that can be used as place markers.

I HAVE UPLOADED OUR BROCHURE DEMO SO YOU CAN GET MORE INFO IN ENGLISH ABOUT US AND MORE PICTURES.

PLEASE REMEMBER THAT THE WEBSITE ¨MOVES¨ when you resize it! Specially the pictures get ¨bigger¨ or smaller¨ when you resize. The same applies to the logos :-)

Once you have created the front page just as the original website I will select it and then we can put the real info and extra pages :-)

Tourists, international people traveling.

Tourism

Coded - Design and coding required

5+ page

Sans Serif

ffffff

• Exactly the same layout of the website mentioned (www.trekvalora.is)
• Everything the same, but with our own logo, texts and photos.
• HOME
• TOURS
• GROUPS
• OUR MOST POPULAR TOURS

```html
<!DOCTYPE html>
<html lang="en">
<head>
<meta charset="utf-8">
<title>Wanderfjordia – Home</title>
<link href="https://fonts.googleapis.com/css2?family=Exo+2:wght@400;500;600&family=Open+Sans:wght@400;600&display=swap" rel="stylesheet">
<style>
:root{
  --red:#e3262b;
  --black:#000;
  --ink:#222;
  --muted:#666;
  --band:#efeff4;
  --white:#fff;
  --sky:#5b86b8;
  --lake:#2f5a78;
}
*{box-sizing:border-box;margin:0;padding:0}
html,body{width:1200px;height:2927px;overflow:hidden;background:var(--white)}
body{position:relative;font-family:"Open Sans",Arial,sans-serif;color:var(--ink)}
.abs{position:absolute}
.heading{font-family:"Exo 2",Arial,sans-serif;font-weight:500;color:var(--ink)}

/* header */
.site-header{left:0;top:0;width:1200px;height:104px;background:var(--white);z-index:3}
.brand{left:111px;top:4px;width:124px;height:124px;border-radius:50%;background:var(--black);border:5px solid var(--white);display:flex;align-items:center;justify-content:center;z-index:4}
.brand span,.foot-brand span{font-family:"Exo 2",Arial,sans-serif;font-weight:600;color:var(--white);font-size:17px}
.nav{left:435px;top:44px;display:flex;gap:0}
.nav a{font-family:"Exo 2",Arial,sans-serif;font-weight:600;font-size:13px;color:var(--ink);text-decoration:none;position:absolute;white-space:nowrap}
.nav a.active{color:var(--red)}
.lang{left:980px;top:35px;width:98px;height:36px;border-radius:18px;background:var(--black);display:flex;align-items:center;justify-content:center;gap:8px}
.lang i{display:block;width:22px;height:15px}
.lang .es{background:linear-gradient(var(--red) 25%,#f4c300 25% 75%,var(--red) 75%)}
.lang .en{background:#1f3b8a}

/* hero */
.hero{left:0;top:104px;width:1200px;height:476px;background:var(--white)}
.hero-panel{position:absolute;left:0;top:0;width:1200px;height:476px}
.p-main{background:linear-gradient(#4d7fb8 0%,#a9c3de 45%,#6b7f95 60%,#2e5673 75%,#23445a 100%);clip-path:polygon(0 0,712px 0,644px 476px,0 476px)}
.p-top{background:linear-gradient(#7f95b0 0%,#c9d3de 40%,#3e4d5f 75%,#151a22 100%);clip-path:polygon(720px 0,1200px 0,1200px 232px,684px 232px)}
.p-bottom{background:linear-gradient(#91a9c4 0%,#dfe6ee 35%,#47596d 65%,#161b20 100%);clip-path:polygon(682px 240px,1200px 240px,1200px 476px,651px 476px)}
.hero-caption{font-family:"Exo 2",Arial,sans-serif;font-size:21px;color:var(--white);white-space:nowrap}

/* tours */
.section-title{font-family:"Exo 2",Arial,sans-serif;font-weight:500;font-size:26px;letter-spacing:.5px;color:var(--ink);text-align:center}
.tabs{left:111px;top:702px;width:976px;height:42px;border-bottom:1px solid #e3e3e3}
.tabs span{position:absolute;top:0;font-family:"Exo 2",Arial,sans-serif;font-size:15px;color:#333;white-space:nowrap}
.tabs span.active{color:var(--red)}
.tabs .bar{position:absolute;left:21px;top:39px;width:100px;height:3px;background:var(--red)}
.tour-card{width:309px}
.tour-photo{width:309px;height:215px;box-shadow:0 18px 18px -14px rgba(0,0,0,.35)}
.tour-name{margin-top:38px;font-family:"Exo 2",Arial,sans-serif;font-size:17px;color:var(--ink)}
.tour-len{margin-top:12px;font-size:13px;color:#888}
.tour-price{margin-top:10px;font-family:"Exo 2",Arial,sans-serif;font-size:17px;color:var(--red)}

/* bands */
.band{left:0;width:1200px;background:var(--band)}
.divider{display:flex;align-items:center;gap:4px}
.divider i{display:block;width:22px;height:2px;background:var(--ink)}
.body-text{font-size:12.5px;line-height:31px;color:#555}
.sub-title{font-family:"Exo 2",Arial,sans-serif;font-weight:500;font-size:25px;color:var(--ink)}
.btn{border:2px solid var(--red);border-radius:28px;color:var(--red);font-family:"Exo 2",Arial,sans-serif;font-size:17px;display:flex;align-items:center;justify-content:center}
.art{border-radius:4px}

/* footer */
.site-footer{left:0;top:2673px;width:1200px;height:254px;background:var(--black);color:var(--white)}
.foot-brand{position:absolute;left:111px;top:39px;width:120px;height:120px;border-radius:50%;border:2px solid var(--white);display:flex;align-items:center;justify-content:center}
.foot-col{position:absolute;top:43px;font-size:12px;line-height:31px}
.foot-col a{display:block;color:var(--white);text-decoration:none}
.foot-head{font-family:"Exo 2",Arial,sans-serif;font-size:18px;letter-spacing:1px;margin-bottom:12px;line-height:24px}
.contact-item{display:flex;align-items:center;gap:14px;font-size:12px;line-height:33px;color:#ddd}
.social-item{display:flex;align-items:center;gap:10px;font-size:11.5px;line-height:29px;color:#ddd}
.social-item i{display:block;width:12px;height:12px;background:#3f6fb5}
.copyright{position:absolute;left:111px;top:184px;font-size:12px}
</style>
</head>
<body>

<header class="abs site-header">
  <div class="abs brand"><span>Wanderfjordia</span></div>
  <nav class="abs nav" style="left:0;top:0">
    <a class="active" style="left:436px;top:46px">HOME</a>
    <a style="left:520px;top:46px">TOURS</a>
    <a style="left:607px;top:46px">GROUPS</a>
    <a style="left:703px;top:46px">RENT A CAR</a>
    <a style="left:818px;top:46px">FLIGHT</a>
    <a style="left:904px;top:46px">CONTACT</a>
  </nav>
  <svg class="abs" style="left:433px;top:64px" width="44" height="14" viewBox="0 0 44 14"><line x1="0" y1="7" x2="16" y2="7" stroke="#222" stroke-width="2"/><line x1="28" y1="7" x2="44" y2="7" stroke="#222" stroke-width="2"/><circle cx="22" cy="6" r="5" fill="#e3262b"/></svg>
  <div class="abs lang"><i class="es"></i><i class="en"></i></div>
</header>

<section class="abs hero">
  <div class="hero-panel p-main" role="img" aria-label="Photo of mountains and lake under a cloudy sky"></div>
  <div class="hero-panel p-top" role="img" aria-label="Photo of a plain and distant peaks under storm clouds"></div>
  <div class="hero-panel p-bottom" role="img" aria-label="Photo of granite towers seen from a road"></div>
  <div class="abs hero-caption" style="left:53px;top:418px">Outdoor adventures in El Chaltén ➔</div>
  <div class="abs hero-caption" style="left:708px;top:190px">Walk with the pre-historic ➔</div>
  <div class="abs hero-caption" style="left:649px;top:428px">Penguin-watch at Punta Tombo ➔</div>
</section>

<h2 class="abs section-title" style="left:0;top:642px;width:1200px">OUR MOST POPULAR TOURS</h2>
<div class="abs tabs">
  <span class="active" style="left:21px">Popular Tours</span>
  <span style="left:159px">Day Tours</span>
  <span style="left:269px">Travel by Air Tours</span>
  <span style="left:437px">Self Drive Tours</span>
  <span style="left:585px">Adventures Tours</span>
  <span style="left:745px">Customize Tours</span>
  <span style="left:899px">Transfer</span>
  <div class="bar"></div>
</div>

<article class="abs tour-card" style="left:111px;top:790px">
  <div class="tour-photo" style="background:linear-gradient(#4f86c6,#c7d6e6 55%,#5d6b62 75%,#3f4a3b)" role="img" aria-label="Photo of hikers before snowy peaks"></div>
  <div class="tour-name">Explore Cueva de las Manos</div>
  <div class="tour-len">length: 3 - 5 hours</div>
  <div class="tour-price">8,800 ISK</div>
</article>
<article class="abs tour-card" style="left:445px;top:790px">
  <div class="tour-photo" style="background:linear-gradient(#5f90c4,#d4dee9 50%,#52663a 68%,#3e4d2e)" role="img" aria-label="Photo of a road across green plains"></div>
  <div class="tour-name">Dive into watersports</div>
  <div class="tour-len">length: 3 - 5 hours</div>
  <div class="tour-price">8,800 ISK</div>
</article>
<article class="abs tour-card" style="left:778px;top:790px">
  <div class="tour-photo" style="background:linear-gradient(#3f78b8,#bccde0 50%,#2d6a84 72%,#1f4d63)" role="img" aria-label="Photo of a turquoise lake and mountains"></div>
  <div class="tour-name">Explore Cueva de las Manos</div>
  <div class="tour-len">length: 3 - 5 hours</div>
  <div class="tour-price">8,800 ISK</div>
</article>

<section class="abs band" style="top:1178px;height:235px">
  <h2 class="abs section-title" style="left:0;top:48px;width:1200px">WELCOME</h2>
  <svg class="abs" style="left:578px;top:85px" width="44" height="14" viewBox="0 0 44 14"><line x1="0" y1="7" x2="16" y2="7" stroke="#222" stroke-width="2"/><line x1="28" y1="7" x2="44" y2="7" stroke="#222" stroke-width="2"/><circle cx="22" cy="6" r="5" fill="#e3262b"/></svg>
  <p class="abs body-text" style="left:150px;top:115px;width:900px;text-align:center">Wanderfjordia es un nuevo tour operator receptivo de confianza especializado en el diseño y prestación de servicios personalizados de incoming en destinos prístinos de la Ecorregión Sub-Antártica y Antártica Chilena.</p>
</section>

<section class="abs" style="left:0;top:1413px;width:1200px;height:437px">
  <div class="abs art" style="left:39px;top:50px;width:362px;height:332px;background:radial-gradient(circle at 50% 55%,#c98b4a,#e2b56b 40%,#f5efe6 72%,#fff)" role="img" aria-label="Illustration of a pile of travel luggage and beach gear"></div>
  <h3 class="abs sub-title" style="left:375px;top:96px">QUIENES SOMOS</h3>
  <svg class="abs" style="left:446px;top:138px" width="44" height="14" viewBox="0 0 44 14"><line x1="0" y1="7" x2="16" y2="7" stroke="#222" stroke-width="2"/><line x1="28" y1="7" x2="44" y2="7" stroke="#222" stroke-width="2"/><circle cx="22" cy="6" r="5" fill="#e3262b"/></svg>
  <p class="abs body-text" style="left:380px;top:166px;width:708px;text-align:justify">Somos una empresa conformada por un idóneo equipo de trabajo que consta de alta motivación, óptimo entrenamiento, elevado capital humano y cuyos integrantes poseen más de 10 años de experiencia trabajando en forma independiente en Turismo Receptivo Regional, Nacional e Internacional. En conjunto nos potenciamos y logramos satisfacer las altas demandas de servicios turísticos requeridos por nuestros clientes.</p>
  <div class="abs btn" style="left:384px;top:310px;width:158px;height:53px">CONTACT US</div>
</section>

<section class="abs band" style="top:1850px;height:394px">
  <h3 class="abs sub-title" style="left:111px;top:94px">MISION</h3>
  <svg class="abs" style="left:132px;top:136px" width="44" height="14" viewBox="0 0 44 14"><line x1="0" y1="7" x2="16" y2="7" stroke="#222" stroke-width="2"/><line x1="28" y1="7" x2="44" y2="7" stroke="#222" stroke-width="2"/><circle cx="22" cy="6" r="5" fill="#e3262b"/></svg>
  <p class="abs body-text" style="left:111px;top:166px;width:684px;text-align:justify">Nuestra misión es ofrecer servicios de Turismo Receptivo para la Región de Magallanes y Antártica Chilena que cumplan con las exigencias de calidad y valor humano que nuestros clientes solicitan. Para lograrlo, trabajamos en conjunto con proveedores turísticos seleccionados y nos enfocamos hacia la excelencia de un servicio personalizado, sirviendo con pasión, experiencia y responsabilidad a cada uno de nuestros clientes.</p>
  <div class="abs art" style="left:820px;top:52px;width:250px;height:278px;background:radial-gradient(circle at 50% 62%,#2f7fc4,#7fb8e2 45%,#f5f6fa 72%)" role="img" aria-label="Illustration of a globe with world landmarks and a plane"></div>
</section>

<section class="abs" style="left:0;top:2244px;width:1200px;height:429px">
  <div class="abs art" style="left:58px;top:68px;width:303px;height:293px;background:radial-gradient(circle at 45% 40%,#bfe3ef,#d9eef5 55%,#fff 75%)" role="img" aria-label="Illustration of suitcases, passports and a folded map"></div>
  <h3 class="abs sub-title" style="left:406px;top:103px">VISION</h3>
  <svg class="abs" style="left:426px;top:145px" width="44" height="14" viewBox="0 0 44 14"><line x1="0" y1="7" x2="16" y2="7" stroke="#222" stroke-width="2"/><line x1="28" y1="7" x2="44" y2="7" stroke="#222" stroke-width="2"/><circle cx="22" cy="6" r="5" fill="#e3262b"/></svg>
  <p class="abs body-text" style="left:406px;top:172px;width:682px;text-align:justify">Nuestra visión es crear una Plataforma de Servicios Logísticos y Turísticos para la Ecorregión Sub-Antártica y Antártica que una toda la oferta turística de la zona a través de una red local, nacional y global de proveedores, con el objetivo de mejorar, a través de la cuidadosa selección de prestadores, la accesibilidad por parte del cliente, la competitividad dentro del mercado, facilitando la inclusión de pequeñas y medianas empresas.</p>
  <div class="abs btn" style="left:412px;top:316px;width:156px;height:52px">READ MORE</div>
</section>

<footer class="abs site-footer">
  <div class="foot-brand"><span>Wanderfjordia</span></div>
  <div class="copyright">@2016, All Right Reserved.</div>
  <div class="foot-col" style="left:351px"><a>Home</a><a>Tours</a><a>Groups</a><a>Rent a Car</a><a>Flight</a><a>Contact</a></div>
  <div class="foot-col" style="left:488px"><a>How To Book</a><a>Booking Terms</a><a>Privacy Policy</a><a>Sitemap</a></div>
  <div class="foot-col" style="left:667px">
    <div class="foot-head">CONTACT US</div>
    <div class="contact-item"><svg width="12" height="14" viewBox="0 0 12 14"><path d="M6 0a5 5 0 0 1 5 5c0 4-5 9-5 9S1 9 1 5a5 5 0 0 1 5-5z" fill="#e3262b"/><circle cx="6" cy="5" r="2" fill="#000"/></svg>27 Harbour Lane, Fjordvik - 104 220</div>
    <div class="contact-item"><svg width="14" height="14" viewBox="0 0 14 14"><rect width="14" height="14" rx="2" fill="#e3262b"/><path d="M4 3l2 2-1 1.5 2.5 2.5L9 8l2 2-1.5 1.5C6 11 3 8 2.5 4.5z" fill="#000"/></svg>08-555-0199</div>
    <div class="contact-item"><svg width="14" height="14" viewBox="0 0 14 14"><rect width="14" height="14" rx="2" fill="#e3262b"/><rect x="3" y="5" width="8" height="6" fill="#000"/><rect x="4" y="2" width="6" height="3" fill="#000"/></svg>08-555-0199</div>
    <div class="contact-item"><svg width="14" height="10" viewBox="0 0 14 10"><rect width="14" height="10" fill="#e3262b"/><path d="M0 0l7 5 7-5" stroke="#000" fill="none"/></svg>info@wanderfjordia.com</div>
  </div>
  <div class="foot-col" style="left:960px">
    <div class="foot-head">CONNECT US</div>
    <div class="social-item"><i></i>Friendwall</div>
    <div class="social-item"><i style="background:#3aa0d8"></i>Chirper</div>
    <div class="social-item"><i style="background:#2a6ca8"></i>ProLink</div>
    <div class="social-item"><i style="background:#d2493a"></i>Circlesphere</div>
    <div class="social-item"><i style="background:#ee8a2b"></i>RSS</div>
  </div>
</footer>

</body>
</html>
```